Grey Fennel Medical Website to make connecting and communicating easier

To create a unique, user-friendly, professional website for patients and professionals to access education/ information, forms, appointments, contact details, and data about us, and for us to have the capacity to link to various cloud-based platforms.
To use the logo design and colour scheme we have just sourced.

WEBSITE to be eye catching, Inspiring and alluring
- efficient and logical
- professional and trustworthy appearance
- health focus "living health matters"
- user friendly
- ability to link with cloud-based software and video conferencing tools/ telehealth
- colours- black/ white teal and ?silver

PAGES:
page 1 - Our clinic and staff, services offered, contact us- address/ map / contact details- social media connections
page 2- patients and visitors - New patient forms to complete, news and patient informtion (educatinal)
page 3 - health professionals -referral forms, research and education
page 3- online appointments
page 4 - Quick links - partners, other services
page 5- privacy policy, disclaimer

HI, Could we please extend the deadline another 5 days, so sorry just struggling with my workload to be able to keep up and I am wanting to liaise more with the designer that I will choose. I am so happy with SketchHarbor and all the designers - thank you! Thank you so much!!

Target Market(s)

Patients - mostly over 60's so the website must be minimal clicks and simple to navigate
Professionals - for education and access forms

Industry/Entity Type

Health Care

Coding

Coded - Design and coding required

Number of Pages Required

5+ page

Font styles to use
Sans Serif
Script

Colors
33b8a4
86cfc6

Requirements
Must have
• WEBSITE to be eye catching, Inspiring and alluring
- efficient and logical
- user friendly

WEBSITE - professional and user friendly
- ability to link with cloud based software and videoconferencing/ telehealth
Nice to have
• clean and crisp presentation
happy for an innovative look
room to add more services and ability to link pages and resources
Should not have
• Please ensure the website is not:
clunky
difficult to navigate
common and cheap looking

```html
<!DOCTYPE html>
<html lang="en">
<head>
<meta charset="utf-8">
<title>Grey Fennel Medical</title>
<link href="https://fonts.googleapis.com/css2?family=Poppins:wght@300;400;500;600;700;800&display=swap" rel="stylesheet">
<style>
:root{
  --teal:#33b8a4;
  --teal-soft:#86cfc6;
  --mint:#eaf7f5;
  --mint-deep:#d8f0ec;
  --ink:#111111;
  --text:#333333;
  --muted:#8a8a8a;
  --line:#e6e6e6;
  --white:#ffffff;
  --silver:#c9cfcf;
}
*{box-sizing:border-box;margin:0;padding:0}
html,body{width:1200px;height:5367px;overflow:hidden}
body{font-family:'Poppins',sans-serif;color:var(--text);background:var(--white);position:relative}
.section{position:absolute;left:0;width:1200px;overflow:hidden}
.abs{position:absolute}
.section-title{position:absolute;left:0;width:1200px;text-align:center;font-size:31px;font-weight:600;color:var(--ink);letter-spacing:1px;display:flex;justify-content:center;align-items:center;gap:18px}
.section-title em{font-style:normal;color:var(--teal)}
.section-title::before,.section-title::after{content:"";width:38px;height:1px;background:#aaa;box-shadow:6px 0 0 0 transparent}
.section-title .dot{width:6px;height:6px;border-radius:50%;background:#aaa;display:inline-block}
.section-lead{position:absolute;left:340px;width:520px;text-align:center;font-size:12px;line-height:22px;color:#555}
.btn-dark{position:absolute;background:var(--ink);color:#fff;font-size:10px;font-weight:600;letter-spacing:.5px;display:flex;align-items:center;justify-content:center}
.arrow-btn{position:absolute;width:33px;height:33px;display:flex;align-items:center;justify-content:center}

/* header */
.header{top:0;height:712px;background:linear-gradient(100deg,#f4f6f6 0%,#eef1f1 45%,#e3e8e8 100%)}
.hero-photo{position:absolute;left:560px;top:121px;width:640px;height:591px;background:linear-gradient(160deg,#eef2f2 0%,#dfe6e6 55%,#cfd9d8 100%)}
.brand-block{position:absolute;left:0;top:0;width:375px;height:67px;background:var(--teal);display:flex;align-items:center;padding-left:60px}
.brand{color:#fff;font-size:22px;font-weight:600}
.topbar-white{position:absolute;left:375px;top:0;width:825px;height:67px;background:#fff}
.contact-item{position:absolute;top:14px;display:flex;gap:16px;align-items:center}
.contact-item .ic{width:38px;height:38px;border-radius:50%;background:var(--teal);display:flex;align-items:center;justify-content:center}
.contact-item .lbl{font-size:10px;font-weight:500;color:var(--ink)}
.contact-item .val{font-size:11px;color:#444;margin-top:4px}
.nav{position:absolute;left:60px;top:67px;width:1080px;height:54px;background:var(--ink);display:flex;align-items:center}
.nav a{position:absolute;font-size:10px;color:#fff;text-decoration:none;font-weight:500;letter-spacing:.3px}
.nav .home{left:2px;top:6px;height:42px;width:75px;background:var(--teal-soft);display:flex;align-items:center;justify-content:center}
.search{position:absolute;left:832px;top:12px;width:225px;height:28px;border:1px solid #555;display:flex;align-items:center;justify-content:space-between;padding:0 8px;font-size:9px;color:#ddd}
.hero-title{position:absolute;left:60px;top:226px;font-size:49px;line-height:56px;font-weight:800;color:var(--teal-soft);letter-spacing:1px;-webkit-text-stroke:1.5px var(--teal)}
.hero-copy{position:absolute;left:60px;top:348px;width:405px;font-size:12px;line-height:22px;color:var(--ink)}

/* departments */
.departments{top:712px;height:850px;background:#fff}
.dept-card{position:absolute;width:210px;height:270px;border:1px solid var(--line);text-align:center;background:#fff}
.dept-card.active{background:var(--teal);border-color:var(--teal)}
.dept-icon{width:78px;height:78px;border-radius:50%;border:2px solid var(--teal);margin:28px auto 0;display:flex;align-items:center;justify-content:center;background:#fff}
.dept-card h3{font-size:15px;font-weight:500;color:var(--ink);margin-top:24px}
.dept-card p{font-size:10.5px;line-height:19px;color:#999;margin:10px 18px 0}
.dept-card .more{font-size:10px;font-weight:600;color:var(--teal);margin-top:10px;letter-spacing:.5px}
.dept-card.active h3,.dept-card.active p,.dept-card.active .more{color:#fff}

/* about */
.about{top:1562px;height:517px;background:var(--mint)}
.blob{position:absolute;background:#f6fcfb;border-radius:50%}
.about-photo{position:absolute;left:146px;top:142px;width:450px;height:285px;background:linear-gradient(135deg,#dfe7ea,#a9bcc5 60%,#6f8a96)}
.about-caption{position:absolute;left:390px;top:367px;width:181px;height:75px;background:var(--ink);color:#fff;font-size:11px;line-height:18px;text-align:center;display:flex;align-items:center;justify-content:center;padding:0 10px}
.about-lead{position:absolute;left:683px;top:140px;width:370px;font-size:11.5px;line-height:20px;font-weight:500;color:var(--ink)}
.about-small{position:absolute;left:683px;top:213px;width:370px;font-size:10px;line-height:17px;color:#999}
.about-list{position:absolute;left:683px;top:266px;list-style:none}
.about-list li{display:flex;align-items:center;gap:14px;font-size:11.5px;color:#444;height:30px}

/* staff */
.staff{top:2079px;height:591px;background:linear-gradient(120deg,#3bbca8 0%,#2fb39f 60%,#43c1ad 100%)}
.staff .section-title{color:#fff}
.staff .section-title::before,.staff .section-title::after{background:#fff}
.staff .section-lead{color:#fff}
.staff-card{position:absolute;top:219px;width:210px;height:298px;background:#fff;text-align:center}
.staff-photo{width:210px;height:156px;background:linear-gradient(180deg,#e8eeef,#c3ced1)}
.staff-card h4{font-size:14px;font-weight:500;color:var(--ink);margin-top:14px}
.staff-card .role{font-size:10px;color:var(--teal);margin-top:6px}
.staff-card .book{display:inline-block;margin-top:12px;width:124px;height:33px;line-height:31px;border:1px solid #ccc;font-size:9px;color:#666;letter-spacing:.3px}
.staff-card .book.on{background:var(--teal);border-color:var(--teal);color:#fff}
.social-rail{position:absolute;left:0;top:0;width:24px;background:#fff}
.social-rail span{display:block;width:24px;height:24px;border-bottom:1px solid #eee;background:#f7f7f7}

/* appointment */
.appointment{top:2670px;height:698px;background:#fff}
.hours-card{position:absolute;left:146px;top:213px;width:240px;height:179px;background:#fff;box-shadow:0 6px 24px rgba(0,0,0,.08);padding:26px 28px}
.hours-card h4{font-size:15px;font-weight:500;color:var(--ink)}
.hours-card p{font-size:10px;color:#aaa;line-height:17px;margin-top:6px}
.hours-card .d{font-size:10px;font-weight:600;color:var(--teal);margin-top:8px}
.hours-card .t{font-size:10px;color:#555}
.appt-photo{position:absolute;left:319px;top:250px;width:562px;height:334px;background:linear-gradient(135deg,#eef1f2,#d7dcdf 55%,#b8c1c5)}
.appt-form{position:absolute;left:708px;top:288px;width:346px;height:335px;background:var(--teal);padding:30px 18px}
.field{position:absolute;height:36px;border:1px solid rgba(255,255,255,.6);color:#fff;font-size:9.5px;display:flex;align-items:center;justify-content:space-between;padding:0 12px}
.swatch{position:absolute;top:611px;width:36px;height:36px}

/* testimonials */
.testimonials{top:3368px;height:486px;background:var(--mint)}
.testi-photo{position:absolute;left:146px;top:138px;width:385px;height:348px;background:linear-gradient(160deg,#e5e9ea,#c9b7a8 55%,#8fa1b0)}
.testi-text{position:absolute;left:637px;top:211px;width:425px;font-size:10px;line-height:19px;color:#666}
.client{position:absolute;left:637px;top:328px;font-size:13px;font-weight:500;color:var(--ink)}

/* blog */
.blog{top:3854px;height:646px;background:#fff}
.blog-card{position:absolute;top:223px;width:271px}
.blog-img{width:271px;height:179px;position:relative}
.blog-date{position:absolute;left:10px;top:8px;background:var(--teal);color:#fff;font-size:9px;font-weight:600;padding:3px 10px}
.blog-card h5{font-size:11.5px;font-weight:500;line-height:21px;color:var(--ink);margin-top:19px}
.blog-card .more{font-size:10px;font-weight:600;color:var(--teal);margin-top:10px;letter-spacing:.4px}

/* map & contact strip */
.map{top:4500px;height:333px;background:linear-gradient(135deg,#eeeeee,#e3e3e3 50%,#ececec)}
.strip{top:4833px;height:84px;background:var(--teal)}
.strip-item{position:absolute;top:20px;display:flex;align-items:center;gap:18px;color:#fff}
.strip-item .ic{width:40px;height:40px;border-radius:50%;background:#fff;display:flex;align-items:center;justify-content:center}
.strip-item .lbl{font-size:9.5px}
.strip-item .val{font-size:11px;margin-top:3px}

/* footer */
.footer{top:4917px;height:450px;background:var(--ink);color:#fff}
.footer h6{font-size:12px;font-weight:600;color:var(--teal);letter-spacing:.5px}
.footer-list{list-style:none;margin-top:16px}
.footer-list li{font-size:10px;height:22px;display:flex;align-items:center;gap:8px}
.footer-list li::before{content:"";width:3px;height:3px;background:#fff;border-radius:50%}
.footer-center{position:absolute;left:381px;top:0;width:436px;height:370px;border-left:1px solid #333;border-right:1px solid #333;text-align:center}
.footer-brand{font-size:24px;font-weight:600;margin-top:80px}
.footer-center p{font-size:10px;line-height:19px;color:#ddd;margin:16px 40px 0}
.subscribe{position:absolute;left:44px;top:272px;width:350px;height:42px;background:#fff;display:flex;align-items:center;justify-content:space-between;padding:3px}
.subscribe span{font-size:9.5px;color:#777;padding-left:10px}
.subscribe b{background:var(--teal);color:#fff;font-size:9.5px;font-weight:600;height:36px;width:90px;display:flex;align-items:center;justify-content:center}
.hours-row{display:flex;font-size:10px;height:30px;align-items:center}
.hours-row span:first-child{width:115px}
.social-sq{position:absolute;top:279px;width:29px;height:29px}
.copyright{position:absolute;left:146px;top:374px;width:908px;border-top:1px solid #333;text-align:center;padding-top:30px;font-size:9.5px;color:#999}
</style>
</head>
<body>

<!-- HEADER / HERO -->
<header class="section header">
  <div class="hero-photo" role="img" aria-label="Photo of a smiling doctor in a white coat holding an X-ray at a bright desk"></div>
  <div class="brand-block"><span class="brand">Grey Fennel Medical</span></div>
  <div class="topbar-white"></div>
  <div class="contact-item" style="left:536px">
    <span class="ic"><svg width="16" height="16" viewBox="0 0 24 24" fill="#fff"><path d="M6.6 10.8a15 15 0 006.6 6.6l2.2-2.2c.3-.3.7-.4 1-.2 1.1.4 2.3.6 3.6.6.6 0 1 .4 1 1V20c0 .6-.4 1-1 1C10.6 21 3 13.4 3 4c0-.6.4-1 1-1h3.5c.6 0 1 .4 1 1 0 1.3.2 2.5.6 3.6.1.3 0 .7-.2 1z"/></svg></span>
    <div><div class="lbl">EMAIL</div><div class="val">medical@greyfennel.com</div></div>
  </div>
  <div class="contact-item" style="left:771px">
    <span class="ic"><svg width="16" height="16" viewBox="0 0 24 24" fill="#fff"><path d="M3 5h18v14H3z" opacity=".9"/><path d="M3 5l9 7 9-7" stroke="var(--teal)" stroke-width="2" fill="none"/></svg></span>
    <div><div class="lbl">PHONE</div><div class="val">+1 234 555 0190</div></div>
  </div>
  <div class="contact-item" style="left:950px">
    <span class="ic"><svg width="16" height="16" viewBox="0 0 24 24" fill="none" stroke="#fff" stroke-width="2"><rect x="4" y="5" width="16" height="15" rx="2"/><path d="M8 3v4M16 3v4M4 10h16"/></svg></span>
    <div><div class="lbl">OFFICE HOURS</div><div class="val">Mon - Sat : 9.00 - 6.00</div></div>
  </div>
  <nav class="nav">
    <a class="home" href="#">HOME</a>
    <a href="#" style="left:107px">ABOUT US</a>
    <a href="#" style="left:196px">OUR SERVICES</a>
    <a href="#" style="left:309px">NEW PATIENTS</a>
    <a href="#" style="left:421px">HEALTH PROFESSIONAL</a>
    <a href="#" style="left:580px">ONLINE APPOINTMENT</a>
    <a href="#" style="left:736px">CONTACT</a>
    <div class="search"><span>Search Here...</span><svg width="11" height="11" viewBox="0 0 24 24" fill="none" stroke="#fff" stroke-width="2.5"><circle cx="10" cy="10" r="7"/><path d="M15 15l6 6"/></svg></div>
  </nav>
  <h1 class="hero-title">LIVING HEALTH<br>MATTERS</h1>
  <p class="hero-copy">Lorem ipsum dolor sit amet, consectetur adipiscing elit, sed do eiusmod tempor incididunt ut labore et dolore magna aliqua. Ut nisi ut aliquip ex ea commodo consequat.</p>
  <div class="btn-dark" style="left:60px;top:440px;width:173px;height:43px">BOOK AN APPOINTMENT</div>
  <div class="arrow-btn" style="left:60px;top:605px;background:var(--teal)"><svg width="10" height="10" viewBox="0 0 10 10" fill="none" stroke="#fff" stroke-width="1.5"><path d="M6.5 1.5L3 5l3.5 3.5"/></svg></div>
  <div class="arrow-btn" style="left:102px;top:605px;background:#222"><svg width="10" height="10" viewBox="0 0 10 10" fill="none" stroke="#fff" stroke-width="1.5"><path d="M3.5 1.5L7 5 3.5 8.5"/></svg></div>
</header>

<!-- DEPARTMENTS -->
<section class="section departments">
  <h2 class="section-title" style="top:74px"><span class="dot"></span>CHOOSE <em>DEPARTMENT</em><span class="dot"></span></h2>
  <p class="section-lead" style="top:130px">Lorem ipsum dolor sit amet, consectetur adipiscing elit, sed do eiusmod tempor exercitation ullamco laboris nisi ut aliquip ex ea commodo consequat.</p>

  <div class="dept-card active" style="left:146px;top:211px">
    <div class="dept-icon"><svg width="40" height="40" viewBox="0 0 40 40" fill="none" stroke="var(--teal)" stroke-width="2"><path d="M6 24c4-2 8-2 12 0l6 2c2 1 1 4-1 3l-6-1"/><path d="M12 14a8 8 0 0116 0c0 6-8 10-8 10s-8-4-8-10z"/><path d="M20 10v8M16 14h8"/></svg></div>
    <h3>General Practice</h3>
    <p>Lorem ipsum dolor sit amet, consectetur adipiscing elit, sed doeri dolore magna aliqua.</p>
    <div class="more">READ MORE &#9656;</div>
  </div>
  <div class="dept-card" style="left:379px;top:211px">
    <div class="dept-icon"><svg width="40" height="40" viewBox="0 0 40 40" fill="none" stroke="var(--ink)" stroke-width="1.6"><circle cx="20" cy="20" r="8"/><path d="M20 4v8M20 28v8M4 20h8M28 20h8M9 9l5 5M26 26l5 5M31 9l-5 5M14 26l-5 5"/></svg></div>
    <h3>Covid-19 Service</h3>
    <p>Lorem ipsum dolor sit amet, consectetur adipiscing elit, sed doeri dolore magna aliqua.</p>
    <div class="more">READ MORE &#9656;</div>
  </div>
  <div class="dept-card" style="left:612px;top:211px">
    <div class="dept-icon"><svg width="40" height="40" viewBox="0 0 40 40" fill="none" stroke="var(--ink)" stroke-width="1.6"><rect x="13" y="6" width="14" height="28" rx="7"/><path d="M13 20h14"/><path d="M20 13v4M18 15h4" stroke="var(--teal)"/></svg></div>
    <h3>Pharmacy</h3>
    <p>Lorem ipsum dolor sit amet, consectetur adipiscing elit, sed doeri dolore magna aliqua.</p>
    <div class="more">READ MORE &#9656;</div>
  </div>
  <div class="dept-card" style="left:844px;top:211px">
    <div class="dept-icon"><svg width="40" height="40" viewBox="0 0 40 40" fill="none" stroke="var(--ink)" stroke-width="1.6"><path d="M8 14c0-4 6-6 12-6s12 2 12 6v4c0 3-3 5-6 5H14c-3 0-6-2-6-5z"/><path d="M14 13v6M20 12v7M26 13v6" stroke="var(--teal)"/><path d="M12 23l2 8M28 23l-2 8"/></svg></div>
    <h3>Dentists</h3>
    <p>Lorem ipsum dolor sit amet, consectetur adipiscing elit, sed doeri dolore magna aliqua.</p>
    <div class="more">READ MORE &#9656;</div>
  </div>

  <div class="dept-card" style="left:146px;top:505px">
    <div class="dept-icon"><svg width="40" height="40" viewBox="0 0 40 40" fill="none" stroke="var(--ink)" stroke-width="1.6"><circle cx="20" cy="8" r="3"/><path d="M20 11v16M12 18h16M16 27l-3 8M24 27l3 8"/><rect x="8" y="20" width="8" height="6" stroke="var(--teal)"/></svg></div>
    <h3>Phsiotherapy</h3>
    <p>Lorem ipsum dolor sit amet, consectetur adipiscing elit, sed doeri dolore magna aliqua.</p>
    <div class="more">READ MORE &#9656;</div>
  </div>
  <div class="dept-card" style="left:379px;top:505px">
    <div class="dept-icon"><svg width="40" height="40" viewBox="0 0 40 40" fill="none" stroke="var(--ink)" stroke-width="1.6"><circle cx="20" cy="14" r="6"/><path d="M8 34c0-7 5-11 12-11s12 4 12 11z"/><path d="M16 27l4 4 4-4" stroke="var(--teal)"/></svg></div>
    <h3>Dermatology</h3>
    <p>Lorem ipsum dolor sit amet, consectetur adipiscing elit, sed doeri dolore magna aliqua.</p>
    <div class="more">READ MORE &#9656;</div>
  </div>
  <div class="dept-card" style="left:612px;top:505px">
    <div class="dept-icon"><svg width="40" height="40" viewBox="0 0 40 40" fill="none" stroke="var(--ink)" stroke-width="1.6"><path d="M14 12c0 8 2 12 0 18 0 3 3 5 6 5s7-3 7-7c0-6-3-8-3-16"/><circle cx="14" cy="7" r="2" stroke="var(--teal)"/><circle cx="19" cy="6" r="1.6" stroke="var(--teal)"/><circle cx="23" cy="7" r="1.4" stroke="var(--teal)"/></svg></div>
    <h3>Podiatry</h3>
    <p>Lorem ipsum dolor sit amet, consectetur adipiscing elit, sed doeri dolore magna aliqua.</p>
    <div class="more">READ MORE &#9656;</div>
  </div>
  <div class="dept-card" style="left:844px;top:505px">
    <div class="dept-icon"><svg width="40" height="40" viewBox="0 0 40 40" fill="none" stroke="var(--ink)" stroke-width="1.6"><path d="M20 5v30"/><path d="M15 9h10M14 15h12M14 21h12M15 27h10" stroke="var(--teal)"/><path d="M10 12c-3 4-3 12 0 16M30 12c3 4 3 12 0 16"/></svg></div>
    <h3>Chiropractic</h3>
    <p>Lorem ipsum dolor sit amet, consectetur adipiscing elit, sed doeri dolore magna aliqua.</p>
    <div class="more">READ MORE &#9656;</div>
  </div>
</section>

<!-- ABOUT -->
<section class="section about">
  <div class="blob" style="left:-120px;top:-60px;width:520px;height:300px"></div>
  <div class="blob" style="left:800px;top:380px;width:560px;height:260px"></div>
  <div class="blob" style="left:1010px;top:-80px;width:300px;height:300px;border-radius:0 0 0 100%"></div>
  <h2 class="section-title" style="top:72px"><span class="dot"></span>ABOUT <em>MEDICAL</em><span class="dot"></span></h2>
  <div class="about-photo" role="img" aria-label="Photo of a dentist examining a patient in a treatment chair"></div>
  <div class="about-caption">We Provide The Best Medical Care For Your Family!</div>
  <p class="about-lead">Lorem ipsum dolor sit amet, consectetur adipiscing elit, sed do eiusmod tempor exercitation ullamco laboris nisi ut that aliquip ex ea commodo consequat.</p>
  <p class="about-small">Lorem ipsum dolor sit amet, consectetur adipiscing elit, sed eiusmod tempor incididunt ut labore et dolore magna aliqua.</p>
  <ul class="about-list">
    <li><svg width="13" height="13" viewBox="0 0 13 13"><circle cx="6.5" cy="6.5" r="6.5" fill="var(--teal)"/><path d="M3.5 6.7l2 2 4-4" stroke="#fff" stroke-width="1.5" fill="none"/></svg>Lorem ipsum dolor sit amet, consectetur.</li>
    <li><svg width="13" height="13" viewBox="0 0 13 13"><circle cx="6.5" cy="6.5" r="6.5" fill="var(--teal)"/><path d="M3.5 6.7l2 2 4-4" stroke="#fff" stroke-width="1.5" fill="none"/></svg>Lorem ipsum dolor sit amet, consectetur.</li>
    <li><svg width="13" height="13" viewBox="0 0 13 13"><circle cx="6.5" cy="6.5" r="6.5" fill="var(--teal)"/><path d="M3.5 6.7l2 2 4-4" stroke="#fff" stroke-width="1.5" fill="none"/></svg>Lorem ipsum dolor sit amet, consectetur.</li>
    <li><svg width="13" height="13" viewBox="0 0 13 13"><circle cx="6.5" cy="6.5" r="6.5" fill="var(--teal)"/><path d="M3.5 6.7l2 2 4-4" stroke="#fff" stroke-width="1.5" fill="none"/></svg>Lorem ipsum dolor sit amet, consectetur.</li>
  </ul>
  <div class="btn-dark" style="left:683px;top:398px;width:112px;height:42px">LEARN MORE</div>
</section>

<!-- STAFF -->
<section class="section staff">
  <h2 class="section-title" style="top:72px"><span class="dot" style="background:#fff"></span>OUR STAFF<span class="dot" style="background:#fff"></span></h2>
  <p class="section-lead" style="top:130px">Lorem ipsum dolor sit amet, consectetur adipiscing elit, sed do eiusmod tempor exercitation ullamco laboris nisi ut aliquip ex ea commodo consequat.</p>
  <div class="arrow-btn" style="left:52px;top:353px;border:1px solid rgba(255,255,255,.7)"><svg width="10" height="10" viewBox="0 0 10 10" fill="none" stroke="#fff" stroke-width="1.5"><path d="M6.5 1.5L3 5l3.5 3.5"/></svg></div>
  <div class="arrow-btn" style="left:1115px;top:353px;background:var(--ink)"><svg width="10" height="10" viewBox="0 0 10 10" fill="none" stroke="#fff" stroke-width="1.5"><path d="M3.5 1.5L7 5 3.5 8.5"/></svg></div>

  <div class="staff-card" style="left:146px">
    <div class="staff-photo" role="img" aria-label="Photo of a nurse in blue scrubs in a hospital corridor"></div>
    <h4>Doctor Name</h4><div class="role">Dentists Specialist</div><span class="book">BOOK APPOINTMENT</span>
  </div>
  <div class="staff-card" style="left:379px">
    <div class="staff-photo" role="img" aria-label="Photo of a doctor with stethoscope"></div>
    <div class="social-rail"><span></span><span></span><span></span><span></span></div>
    <h4>Doctor Name</h4><div class="role">Dentists Specialist</div><span class="book on">BOOK APPOINTMENT</span>
  </div>
  <div class="staff-card" style="left:612px">
    <div class="staff-photo" role="img" aria-label="Photo of a doctor in a white coat"></div>
    <h4>Doctor Name</h4><div class="role">Dentists Specialist</div><span class="book">BOOK APPOINTMENT</span>
  </div>
  <div class="staff-card" style="left:844px">
    <div class="staff-photo" role="img" aria-label="Photo of a doctor holding a clipboard"></div>
    <h4>Doctor Name</h4><div class="role">Dentists Specialist</div><span class="book">BOOK APPOINTMENT</span>
  </div>
</section>

<!-- APPOINTMENT -->
<section class="section appointment">
  <h2 class="section-title" style="top:76px"><span class="dot"></span>BOOK AN <em>APPOINTMENT</em><span class="dot"></span></h2>
  <p class="section-lead" style="top:132px">Lorem ipsum dolor sit amet, consectetur adipiscing elit, sed do eiusmod tempor exercitation ullamco laboris nisi ut aliquip ex ea commodo consequat.</p>
  <div class="appt-photo" role="img" aria-label="Photo of a physiotherapist treating a patient's neck and shoulder"></div>
  <div class="hours-card">
    <h4>Opening Hours</h4>
    <p>Lorem ipsum dolor sit consectetur adipiscing elit, sed do.</p>
    <div class="d">MONDAY TO FRIDAY</div><div class="t">9.00 AM - 6.00 PM</div>
    <div class="d">SATURDAY</div><div class="t">9.00 AM - 6.00 PM</div>
    <div class="d">SUNDAY <span class="t" style="font-weight:400">- Closed</span></div>
  </div>
  <div class="appt-form">
    <div class="field" style="left:18px;top:30px;width:150px">Select Department <span>&#8964;</span></div>
    <div class="field" style="left:178px;top:30px;width:150px">Select Doctor <span>&#8964;</span></div>
    <div class="field" style="left:18px;top:75px;width:150px">Your Name</div>
    <div class="field" style="left:178px;top:75px;width:150px">Your Number</div>
    <div class="field" style="left:18px;top:120px;width:150px">Date</div>
    <div class="field" style="left:178px;top:120px;width:150px">Time</div>
    <div class="field" style="left:18px;top:165px;width:310px;height:88px;align-items:flex-start;padding-top:10px">Special Request...</div>
    <div class="btn-dark" style="left:114px;top:264px;width:118px;height:42px">BOOK NOW</div>
  </div>
  <div class="swatch" style="left:229px;background:var(--ink)"></div>
  <div class="swatch" style="left:275px;background:#eeeeee"></div>
  <div class="swatch" style="left:319px;background:var(--teal)"></div>
  <div class="swatch" style="left:365px;background:var(--teal-soft)"></div>
</section>

<!-- TESTIMONIALS -->
<section class="section testimonials">
  <h2 class="section-title" style="top:74px"><span class="dot"></span>CLIENT <em>TESTIMONIALS</em><span class="dot"></span></h2>
  <div class="testi-photo" role="img" aria-label="Photo of a smiling carer with an elderly woman in a wheelchair"></div>
  <svg class="abs" style="left:637px;top:144px" width="54" height="40" viewBox="0 0 54 40" fill="var(--teal)"><path d="M0 40V22C0 9 7 2 20 0v8c-6 2-9 6-9 12h9v20zM30 40V22C30 9 37 2 50 0v8c-6 2-9 6-9 12h9v20z"/></svg>
  <p class="testi-text">Lorem ipsum dolor sit amet, consectetur adipiscing elit, sed do eiusmod tempor incididunt ut labore et dolore magna aliqua. Ut enim ad minim veniam, quis nostrud exercitation ullamco laboris nisi ut aliquip ex ea commodo consequat. Duis aute irure dolor in reprehenderit in voluptate velit esse cillum dolore eu fugiat nulla pariatur.</p>
  <div class="client">&ndash;&nbsp; Client Name</div>
  <div class="arrow-btn" style="left:637px;top:382px;width:30px;height:30px;background:var(--teal)"><svg width="10" height="10" viewBox="0 0 10 10" fill="none" stroke="#fff" stroke-width="1.5"><path d="M6.5 1.5L3 5l3.5 3.5"/></svg></div>
  <div class="arrow-btn" style="left:681px;top:382px;width:30px;height:30px;background:#222"><svg width="10" height="10" viewBox="0 0 10 10" fill="none" stroke="#fff" stroke-width="1.5"><path d="M3.5 1.5L7 5 3.5 8.5"/></svg></div>
</section>

<!-- BLOG -->
<section class="section blog">
  <h2 class="section-title" style="top:78px"><span class="dot"></span>RECENT <em>BLOG</em><span class="dot"></span></h2>
  <p class="section-lead" style="top:134px">Lorem ipsum dolor sit amet, consectetur adipiscing elit, sed do eiusmod tempor exercitation ullamco laboris nisi ut aliquip ex ea commodo consequat.</p>
  <article class="blog-card" style="left:146px">
    <div class="blog-img" role="img" aria-label="Photo of a physiotherapist helping a patient walk" style="background:linear-gradient(135deg,#e8ecee,#b7c2c9)"><span class="blog-date">9 OCT 2020</span></div>
    <h5>Lorem ipsum dolor sit amet, consectetur aliquip ex ea commodo consequat.</h5>
    <div class="more">LEARN MORE &#9656;</div>
  </article>
  <article class="blog-card" style="left:465px">
    <div class="blog-img" role="img" aria-label="Photo of a rehabilitation exercise session in a clinic" style="background:linear-gradient(135deg,#dfe9f1,#9fb6c8)"><span class="blog-date">9 OCT 2020</span></div>
    <h5>Lorem ipsum dolor sit amet, consectetur aliquip ex ea commodo consequat.</h5>
    <div class="more">LEARN MORE &#9656;</div>
  </article>
  <article class="blog-card" style="left:783px">
    <div class="blog-img" role="img" aria-label="Photo of a clinician in blue gloves treating a patient" style="background:linear-gradient(135deg,#eef0f2,#c6d3e4)"><span class="blog-date">9 OCT 2020</span></div>
    <h5>Lorem ipsum dolor sit amet, consectetur aliquip ex ea commodo consequat.</h5>
    <div class="more">LEARN MORE &#9656;</div>
  </article>
</section>

<!-- MAP -->
<section class="section map" role="img" aria-label="Street map showing the clinic location"></section>

<!-- CONTACT STRIP -->
<section class="section strip">
  <div class="strip-item" style="left:146px">
    <span class="ic"><svg width="16" height="16" viewBox="0 0 24 24" fill="var(--teal)"><path d="M6.6 10.8a15 15 0 006.6 6.6l2.2-2.2c.3-.3.7-.4 1-.2 1.1.4 2.3.6 3.6.6.6 0 1 .4 1 1V20c0 .6-.4 1-1 1C10.6 21 3 13.4 3 4c0-.6.4-1 1-1h3.5c.6 0 1 .4 1 1 0 1.3.2 2.5.6 3.6.1.3 0 .7-.2 1z"/></svg></span>
    <div><div class="lbl">EMAIL</div><div class="val">medical@greyfennel.com</div></div>
  </div>
  <div class="strip-item" style="left:454px">
    <span class="ic"><svg width="16" height="16" viewBox="0 0 24 24"><path d="M3 5h18v14H3z" fill="var(--teal)"/><path d="M3 5l9 7 9-7" stroke="#fff" stroke-width="2" fill="none"/></svg></span>
    <div><div class="lbl">PHONE</div><div class="val">+1 234 555 0190</div></div>
  </div>
  <div class="strip-item" style="left:767px">
    <span class="ic"><svg width="16" height="16" viewBox="0 0 24 24" fill="none" stroke="var(--teal)" stroke-width="2"><rect x="4" y="5" width="16" height="15" rx="2"/><path d="M8 3v4M16 3v4M4 10h16"/></svg></span>
    <div><div class="val">Mon - Sat : 9.00 - 6.00</div></div>
  </div>
</section>

<!-- FOOTER -->
<footer class="section footer">
  <div class="abs" style="left:146px;top:76px">
    <h6>OUR SERVICES</h6>
    <ul class="footer-list">
      <li>General Practice</li><li>Covid-19 Service</li><li>Pharmacy</li><li>Dentists</li>
      <li>Phsiotherapy</li><li>Dermatology</li><li>Podiatry</li><li>Chiropractic</li>
    </ul>
  </div>
  <div class="footer-center">
    <div class="footer-brand">Grey Fennel Medical</div>
    <p>Lorem ipsum dolor sit amet, consectetur adipiscing elit, sed do Duis aute irure dolor in reprehenderit in voluptate velit esse cillum dolore eu fugiat nulla pariatur.</p>
    <div class="abs" style="left:44px;top:226px;font-size:13px;font-weight:600;color:var(--teal)">Email Address</div>
    <div class="subscribe"><span>Enter Email Address</span><b>SUBCRIBE</b></div>
  </div>
  <div class="abs" style="left:879px;top:76px;width:200px">
    <h6>OPENING HOURS</h6>
    <div style="margin-top:8px">
      <div class="hours-row"><span>Monday - Friday</span><span>9.00 - 6.00</span></div>
      <div class="hours-row"><span>Saturday</span><span>9.00 - 6.00</span></div>
      <div class="hours-row"><span>Sunday</span><span>Closed</span></div>
    </div>
    <h6 style="margin-top:42px">QUICK CONNECTED</h6>
  </div>
  <div class="social-sq" style="left:879px;background:#3b5998" aria-label="Social link"></div>
  <div class="social-sq" style="left:923px;background:#1da1f2" aria-label="Social link"></div>
  <div class="social-sq" style="left:967px;background:#0077b5" aria-label="Social link"></div>
  <div class="social-sq" style="left:1011px;background:#d6336c" aria-label="Social link"></div>
  <div class="copyright">&copy; 2020 Grey Fennel Medical. &nbsp;All rights reserved &nbsp;| &nbsp;Privacy &nbsp;| &nbsp;Terms of Use</div>
</footer>

</body>
</html>
```